Sophisticated, clean website reflecting my feminine, playful side to sell my abstract art,

I need a website no more than 3 pages to showcase my paintings, a little about me and some contact info. I do abstracts so looking for something a little edgy, yet feminine and current.
Updates

Hi there, These are some artists websites that I Iike: Marnelvoss.com (I like how airy it is) peterwallombry.com garethpolvens.com (I like how it scrolls) I'll need a place for a photo ( a headshot-i do not have it yet so I'll need to be able to upload that later) as well as an area for my bio. Also, it's important that I will be able to upload any new photos and descriptions easily so it should be user friendly. Lastly, I like in a sunny place so would like to have this seem upbeat and playful as that is how i like to paint. thanks-I'm trying to upload my photos now -

Target Market(s)

ppl ages 35-70 who want large scale art for their homes

Industry/Entity Type

art

Coding

Coded - Design and coding required

Number of Pages Required

3 page

Colors

Designer to choose colors to be used in the design.

Requirements
Must have
• photos of my art, a place for my bio, be easy to reach me. tasteful-nothing too "in your face" -my clients are pretty high end and organized. They like clean lines
Nice to have
• sophisticated background, muted tones in the back-similar clean font throughout-no cursive
Should not have
• too many dark areas. Too many blocks of color. Too serious.

```html
<!DOCTYPE html>
<html lang="en">
<head>
<meta charset="utf-8">
<title>Lena Marlowe — Abstract Art</title>
<link rel="stylesheet" href="https://fonts.googleapis.com/css2?family=Crimson+Text:wght@400;600&family=Roboto:wght@700&family=Poppins:wght@400&display=swap">
<style>
  :root {
    --ink: #111111;
    --paper: #ffffff;
    --accent-rose: #c07a63;
    --sage: #8fa98a;
    --field: #f2f2f2;
    --placeholder: #6b6b6b;
    --rule: #8a8a8a;
    --serif: "Crimson Text", Georgia, serif;
    --sans: "Roboto", Arial, sans-serif;
    --ui: "Poppins", Arial, sans-serif;
  }
  * { box-sizing: border-box; margin: 0; padding: 0; }
  html, body { width: 1200px; height: 2822px; overflow: hidden; background: var(--paper); color: var(--ink); }
  body { position: relative; font-family: var(--serif); }
  .abs { position: absolute; }
  .center-text { left: 0; width: 1200px; text-align: center; }

  /* Header */
  .site-header { top: 0; left: 0; width: 1200px; height: 167px; box-shadow: 0 12px 22px rgba(0,0,0,0.10); background: var(--paper); z-index: 2; }
  .brand { top: 40px; left: 85px; display: flex; align-items: center; gap: 10px; font-family: var(--serif); font-size: 22px; font-weight: 600; color: var(--ink); }
  .brand-square { width: 26px; height: 26px; background: var(--ink); }
  .main-nav a { position: absolute; top: 46px; font-size: 20px; color: var(--ink); text-decoration: none; }
  .site-title { top: 102px; font-family: var(--sans); font-weight: 700; font-size: 40px; letter-spacing: 0.33em; text-indent: 0.33em; line-height: 48px; }

  .hero-art { top: 167px; left: 0; width: 1200px; height: 579px;
    background: linear-gradient(120deg, #d9dcd6 0%, #4d9a4a 25%, #2f8f3a 45%, #7cc150 60%, #e6e0c9 80%, #6f6f6a 100%);
    box-shadow: 0 18px 30px rgba(0,0,0,0.12); }

  /* About */
  .portrait { top: 851px; left: 213px; width: 287px; height: 286px; background: linear-gradient(180deg, #e6e6e8 0%, #d8c7c2 55%, #e774a4 100%); }
  .eyebrow { top: 876px; left: 620px; font-size: 22px; color: var(--accent-rose); }
  .about-title { top: 912px; left: 620px; font-size: 31px; font-weight: 400; letter-spacing: 0.02em; }
  .about-copy { top: 960px; left: 620px; width: 420px; font-size: 17px; line-height: 19px; }
  .btn-outline { border: 1px solid var(--ink); background: var(--paper); color: var(--ink); text-align: center; }
  .view-more { top: 1080px; left: 620px; width: 106px; height: 29px; font-size: 17px; line-height: 27px; }

  /* Gallery */
  .section-title { top: 1234px; font-size: 33px; font-weight: 400; letter-spacing: 0.04em; left: -24px; }
  .artwork { top: 1301px; left: 176px; width: 813px; height: 506px;
    background: linear-gradient(110deg, #3b3a33 0%, #2c6a4a 30%, #e8e3d6 45%, #b5602b 60%, #1f9bc0 78%, #d5d4d0 100%); }
  .carousel-arrow { top: 1532px; width: 44px; height: 44px; }
  .art-name { top: 1832px; left: -24px; font-size: 39px; font-weight: 400; letter-spacing: 0.03em; }
  .art-price { top: 1900px; left: -24px; font-family: var(--ui); font-size: 33px; }
  .add-to-cart { top: 1971px; left: 476px; width: 203px; height: 58px; font-family: var(--ui); font-size: 22px; line-height: 56px; }

  /* Social */
  .social-line { left: -4px; font-size: 32px; font-weight: 600; letter-spacing: 0.08em; text-indent: 0.08em; line-height: 40px; }

  /* Contact */
  .form-title { top: 2303px; left: -8px; font-size: 38px; line-height: 37px; font-weight: 400; }
  .field { left: 379px; width: 442px; background: var(--field); font-size: 13px; color: var(--placeholder); text-align: center; letter-spacing: 0.02em; padding-top: 7px; }
  .send { top: 2684px; left: 556px; width: 88px; height: 28px; font-size: 14px; line-height: 26px; letter-spacing: 0.04em; }

  /* Footer */
  .footer-rule { top: 2759px; left: 0; width: 1200px; height: 1px; background: var(--rule); }
  .copyright { top: 2786px; font-family: var(--ui); font-size: 14px; }
</style>
</head>
<body>
  <header class="abs site-header">
    <div class="abs brand"><span class="brand-square"></span>Lena Marlowe</div>
    <nav class="main-nav">
      <a style="left:431px">About me</a>
      <a style="left:565px">Gallery</a>
      <a style="left:680px">Contact us</a>
    </nav>
    <h1 class="abs center-text site-title">LENA MARLOWE</h1>
  </header>

  <div class="abs hero-art" role="img" aria-label="Abstract painting in greens, teal and ochre brushstrokes"></div>

  <section>
    <div class="abs portrait" role="img" aria-label="Headshot of the artist"></div>
    <p class="abs eyebrow">Bio Graphy</p>
    <h2 class="abs about-title">ABOUT ME</h2>
    <p class="abs about-copy">Lorem ipsum dolor sit amet, consectetur estor adipi isicing elit, sed do eiusmod tempor este uterre incididui unt ut labore et dolore magna aliquaas. Ut enim ad minim veniam, quis mot nostrud desto exercitation est ullamco laboris nisi ut se aliquip ex ea commodos consequat.</p>
    <div class="abs btn-outline view-more">View More</div>
  </section>

  <section>
    <h2 class="abs center-text section-title">GALLERY</h2>
    <div class="abs artwork" role="img" aria-label="Abstract painting in dark green, white, orange and turquoise"></div>
    <svg class="abs carousel-arrow" style="left:111px" viewBox="0 0 44 44" aria-label="Previous">
      <circle cx="22" cy="22" r="22" fill="var(--sage)"/>
      <path d="M31 22H13M20 15l-7 7 7 7" stroke="#fff" stroke-width="2.5" fill="none" stroke-linecap="round" stroke-linejoin="round"/>
    </svg>
    <svg class="abs carousel-arrow" style="left:1000px" viewBox="0 0 44 44" aria-label="Next">
      <circle cx="22" cy="22" r="22" fill="var(--sage)"/>
      <path d="M13 22h18M24 15l7 7-7 7" stroke="#fff" stroke-width="2.5" fill="none" stroke-linecap="round" stroke-linejoin="round"/>
    </svg>
    <h3 class="abs center-text art-name">THE TIDEPOOL</h3>
    <p class="abs center-text art-price">$300.</p>
    <div class="abs btn-outline add-to-cart">ADD TO CARD</div>
  </section>

  <section>
    <p class="abs center-text social-line" style="top:2132px">FOLLOW LMARLOWEART ON SNAPFOLIO</p>
    <p class="abs center-text social-line" style="top:2181px">@LMPAINTS ON CLIPSTREAM</p>
  </section>

  <section>
    <h2 class="abs center-text form-title">Fill the form get in<br>touch with me</h2>
    <div class="abs field" style="top:2412px;height:33px">Enter your name here</div>
    <div class="abs field" style="top:2468px;height:33px">Enter your email here</div>
    <div class="abs field" style="top:2527px;height:33px">Enter your phone here</div>
    <div class="abs field" style="top:2583px;height:75px">Enter your message here</div>
    <div class="abs btn-outline send">SEND</div>
  </section>

  <footer>
    <div class="abs footer-rule"></div>
    <p class="abs center-text copyright">Copyright lmarloweart 2021 All Rights Reserved</p>
  </footer>
</body>
</html>
```